Corvane Paintless Dent Removal

Our company works on vehicles removing dents using a highly skilled trade which the metal is massaged out with special tools without disturbing the original paint, hence paintless dent removal. Besides keeping the paint and metal original its also very environmentally friendly since no paint or toxic fillers are used. Also we we are one of the most experienced companies in the business with 25 years

Target Market(s)

Retail Automobile consumers, Auto Dealerships and Auto Body Shops

Industry/Entity Type

Auto Repair

Contact Information for Business Card

Dale Hollister
PO Box 518 Brookmere, NY 11962
631-555-0148
corvanepdr@mailbox-example.com
website corvanepdr.example
youtube corvane paintless dent removal
25 years of experience removing Dents, Dings and Hail Damage

Font styles to use
Serif
Sans Serif

Colors

Designer to choose colors to be used in the design.

Requirements
Must have
• I do like things that are simple but classy and somewhat bold, also I like my logo so that should be somewhat important

```html
<!DOCTYPE html>
<html lang="en">
<head>
<meta charset="utf-8">
<title>Corvane Paintless Dent Removal – Business Card</title>
<link href="https://fonts.googleapis.com/css2?family=Roboto:wght@400;700;900&family=Roboto+Condensed:wght@700&display=swap" rel="stylesheet">
<style>
  :root {
    --navy: #112a4d;
    --green: #7dbb2a;
    --paper: #f4f4f2;
    --ink: #3d3d3d;
    --rule: #8a8a8a;
    --backdrop: #e6e3de;
    --gold: #c9a23e;
    --white: #ffffff;
  }
  * { margin: 0; padding: 0; box-sizing: border-box; }
  html, body { width: 1200px; height: 960px; overflow: hidden; }
  body {
    background: var(--backdrop);
    font-family: "Roboto", Arial, sans-serif;
    position: relative;
  }
  .card {
    position: absolute;
    width: 600px;
    height: 343px;
    box-shadow: 0 3px 8px rgba(0,0,0,0.25);
  }
  .card--front { left: 314px; top: 113px; background: var(--paper); }
  .card--back { left: 311px; top: 472px; background: var(--navy); }

  .holder-name {
    position: absolute;
    right: 35px;
    top: 47px;
    font-family: "Roboto Condensed", "Arial Narrow", sans-serif;
    font-weight: 700;
    font-size: 22px;
    color: var(--navy);
    letter-spacing: 0.3px;
  }
  .name-tab {
    position: absolute;
    right: 0;
    top: 44px;
    width: 15px;
    height: 31px;
    background: var(--navy);
  }

  .brand {
    position: absolute;
    display: flex;
    align-items: center;
    gap: 12px;
    font-family: "Roboto", Arial, sans-serif;
    font-weight: 900;
    line-height: 1.05;
  }
  .brand__dot {
    flex: none;
    border-radius: 50%;
    background: var(--green);
  }
  .card--front .brand { left: 22px; top: 140px; color: var(--navy); font-size: 26px; }
  .card--front .brand__dot { width: 34px; height: 34px; }
  .card--back .brand { left: 130px; top: 125px; color: var(--white); font-size: 32px; }
  .card--back .brand__dot { width: 42px; height: 42px; }

  .divider {
    position: absolute;
    left: 38px;
    top: 229px;
    width: 524px;
    height: 1.5px;
    background: var(--rule);
  }
  .contact-list {
    position: absolute;
    left: 38px;
    top: 253px;
    list-style: none;
    font-size: 14px;
    color: var(--ink);
  }
  .contact-list li {
    display: flex;
    align-items: center;
    height: 19px;
  }
  .contact-list svg { width: 13px; height: 13px; margin-right: 9px; fill: var(--navy); }
  .address {
    position: absolute;
    right: 35px;
    top: 255px;
    text-align: right;
    font-style: normal;
    font-size: 14px;
    line-height: 19px;
    color: var(--ink);
  }

  .experience-seal {
    position: absolute;
    left: 506px;
    top: 19px;
    width: 68px;
    height: 68px;
    border-radius: 50%;
    background: radial-gradient(circle, #1a1a1a 0 55%, var(--gold) 56% 100%);
  }
  .back-url {
    position: absolute;
    left: 0;
    right: 0;
    top: 280px;
    text-align: center;
    color: var(--white);
    font-size: 14px;
    letter-spacing: 5px;
  }
</style>
</head>
<body>
  <section class="card card--front">
    <h1 class="holder-name">DALE HOLLISTER</h1>
    <span class="name-tab"></span>

    <div class="brand">
      <span class="brand__dot"></span>
      <span class="brand__name">Corvane<br>Paintless Dent Removal</span>
    </div>

    <div class="divider"></div>

    <ul class="contact-list">
      <li>
        <svg viewBox="0 0 24 24"><path d="M6.6 10.8c1.4 2.8 3.8 5.1 6.6 6.6l2.2-2.2c.3-.3.7-.4 1-.2 1.1.4 2.3.6 3.6.6.6 0 1 .4 1 1V20c0 .6-.4 1-1 1C10.6 21 3 13.4 3 4c0-.6.4-1 1-1h3.5c.6 0 1 .4 1 1 0 1.3.2 2.5.6 3.6.1.3 0 .7-.2 1z"/></svg>
        631-555-0148
      </li>
      <li>
        <svg viewBox="0 0 24 24"><path d="M2 5h20v14H2z M3.5 6.5 12 12l8.5-5.5" fill="var(--navy)"/><path d="M3 6l9 6 9-6" stroke="#fff" stroke-width="1.6" fill="none"/></svg>
        corvanepdr@mailbox-example.com
      </li>
      <li>
        <svg viewBox="0 0 24 24"><rect x="3" y="5" width="18" height="14" rx="3"/></svg>
        corvane paintless dent removal
      </li>
    </ul>

    <address class="address">
      PO Box 518<br>
      Brookmere, NY 11962<br>
      www.corvanepdr.example
    </address>
  </section>

  <section class="card card--back">
    <div class="experience-seal" role="img" aria-label="25 years of experience seal"></div>
    <div class="brand">
      <span class="brand__dot"></span>
      <span class="brand__name">Corvane<br>Paintless Dent Removal</span>
    </div>
    <p class="back-url">www.corvanepdr.example</p>
  </section>
</body>
</html>
```